Transform Your Giving

I need a tri-fold brochure that will fit in a standard number 10 business envelope. Meadowlark and Allied Services is a charitable nonprofit. The goal of this brochure is to stimulate people into thinking about other ways to make a donation. The design should communicate the essential information on donation options, create a sense of professional integrity, be graphically sharp, easy to read and laid out in a way that doesn't make the material appear crowded.

```html
<!DOCTYPE html>
<html lang="en">
<head>
<meta charset="utf-8">
<title>Transform Your Giving – Meadowlark and Allied Services</title>
<link href="https://fonts.googleapis.com/css2?family=Montserrat:ital,wght@0,400;0,500;0,600;0,700;0,800;1,500;1,600;1,700&display=swap" rel="stylesheet">
<style>
:root{
  --navy:#2e2a76;
  --green:#3fa535;
  --green-dark:#2f8a2a;
  --ink:#2b2b33;
  --paper:#ffffff;
  --paper-soft:#eef0f1;
  --stage:#e4e5e7;
  --umber:#3a2b24;
  --accent:#d8652c;
}
*{box-sizing:border-box;margin:0;padding:0}
html,body{width:1200px;height:3575px;overflow:hidden}
body{background:var(--stage);font-family:'Montserrat',sans-serif;color:var(--ink);position:relative}
.spread{position:absolute;left:30px;width:1140px;height:876px;display:flex;box-shadow:0 10px 30px rgba(0,0,0,.18);background:var(--paper)}
.spread--outside{top:880px}
.spread--inside{top:1816px}
.panel{position:relative;width:380px;height:876px;overflow:hidden}
.panel-bg{position:absolute;inset:0}
.photo{position:absolute}
.copy{position:absolute;left:26px;right:26px}
p{font-size:11.6px;line-height:1.42}
.center{text-align:center}
.white{color:#fff}
.green{color:var(--green)}
.navy{color:var(--navy)}
h2.impact{font-size:19px;font-weight:700;color:var(--navy);margin-bottom:18px}
h2.impact span{color:var(--green)}
.gift-list{list-style:none;margin-top:22px}
.gift-list li{font-size:14px;font-weight:600;color:var(--green);margin-bottom:12px;padding-left:16px;position:relative}
.gift-list li::before{content:"";position:absolute;left:0;top:7px;width:5px;height:5px;border-radius:50%;background:var(--navy)}
.follow{font-size:12px;font-weight:600;color:#fff}
.rule{height:1px;background:rgba(255,255,255,.75);margin:46px 50px 0}
.lead{font-size:11.4px;font-weight:600;line-height:1.45}
.quote{font-size:14px;font-style:italic;font-weight:500}
.quote-name{font-size:17px;font-style:italic;font-weight:700}
.link-lg{font-size:16px;font-weight:700;font-style:italic}
.contact-h{font-size:15.5px;font-weight:700;font-style:italic}
.phone{font-size:22px;font-weight:700}
.brand{font-size:34px;font-weight:800;color:#fff;letter-spacing:1px}
.brand-row{display:flex;align-items:center;justify-content:center;gap:10px}
.brand-dot{width:14px;height:14px;border-radius:50%;background:#fff}
.tag{font-size:22px;font-weight:500;color:#fff}
.headline{font-size:40px;line-height:1.02;font-weight:800;color:var(--green);margin:10px 0 14px}
.sub{font-size:14px;color:#fff;line-height:1.5}
h3.sect{font-size:18.5px;font-weight:600;line-height:1.2}
h3.sect-sm{font-size:16.5px;font-weight:600;line-height:1.2}
.kicker{font-size:12.6px;font-weight:700;font-style:italic;line-height:1.35}
.kicker-sm{font-size:11.5px;font-weight:700;font-style:italic;line-height:1.3}
h4.how{font-size:19px;font-weight:500;margin:16px 0 8px}
h4.how-sm{font-size:12.5px;font-weight:600;margin:12px 0 6px}
.dots{padding-left:30px;margin:8px 0}
.dots li{font-size:11.4px;line-height:1.42;margin-bottom:12px}
.small p{font-size:11px;line-height:1.38}
.qcd h3.sect-sm{font-size:15px;line-height:1.2}
.qcd p.kicker-sm{font-size:10.4px;line-height:1.3;margin-top:6px}
.qcd p.qcd-body{font-size:9.4px;line-height:1.34;text-align:justify}
.qcd h4.how-sm{font-size:11.5px;margin:9px 0 4px}
</style>
</head>
<body>

<!-- OUTSIDE SPREAD -->
<section class="spread spread--outside">

  <!-- Back panel: impact -->
  <article class="panel">
    <div class="panel-bg" style="background:linear-gradient(180deg,#fff 0%,var(--paper-soft) 100%)"></div>
    <div class="copy" style="top:40px">
      <h2 class="impact">THE IMPACT OF <span>YOUR GIFT</span></h2>
      <p style="text-align:justify">Your generosity drives our mission. With every Smart gift you're supporting Meadowlark and Allied Services. Join our community of Smart Givers today and make an enduring impact. With Smart Giving your generosity reaches further. Begin your Smart Giving journey with us today.</p>
      <ul class="gift-list">
        <li>Stocks and Securities</li>
        <li>DAFs</li>
        <li>QCDs</li>
        <li>Crypto</li>
        <li>Charitable Annuity</li>
      </ul>
    </div>
    <div class="photo" role="img" aria-label="Photo of a person sitting on a grassy hill silhouetted against a cloudy sunset sky" style="left:0;right:0;top:420px;bottom:0;background:linear-gradient(180deg,#b9b6ad 0%,#8f8a80 45%,#4c4942 78%,#1f1f1c 100%)"></div>
    <svg style="position:absolute;left:0;top:410px" width="380" height="60" viewBox="0 0 380 60" aria-hidden="true">
      <path d="M0 0H380V10C290 48 170 58 0 30Z" fill="#eceeef"/>
    </svg>
  </article>

  <!-- Inner flap: contact -->
  <article class="panel">
    <div class="panel-bg" style="background:linear-gradient(160deg,#2c2522 0%,var(--umber) 55%,#5a3f30 100%)" role="img" aria-label="Dark warm photo of hands holding hands"></div>
    <div class="panel-bg" style="top:360px;background:var(--navy)"></div>
    <svg style="position:absolute;left:0;top:330px" width="380" height="70" viewBox="0 0 380 70" aria-hidden="true">
      <path d="M0 40C120 10 260 0 380 18V42C260 26 130 36 0 58Z" fill="var(--green)"/>
      <path d="M0 58C130 36 260 26 380 42V70H0Z" fill="var(--navy)"/>
    </svg>
    <div class="copy center" style="top:46px">
      <p class="follow">Follow us:</p>
      <div class="rule"></div>
      <p class="white" style="margin-top:40px;font-size:10.8px">This material has been prepared for informational purposes only and is not intended to provide tax, accounting, or legal advice. Meadowlark and Allied Services is not a professional fiduciary organization.</p>
      <p class="white" style="margin-top:16px;font-size:10.8px">Please consult with your tax advisor or financial professional before making a decision about Smart Giving.</p>
    </div>
    <div class="copy center white" style="top:408px">
      <p class="lead">To learn more about Smart Giving Options and how they can benefit you and Meadowlark and Allied Services, please reach out to our team. We're here to help you navigate these giving methods and answer any question you may have.</p>
      <p class="quote" style="margin-top:22px">Being kind to others is a way of being good to yourself.</p>
      <p class="quote-name" style="margin-top:10px">Harriet Lindqvist</p>
      <p style="margin-top:20px;font-weight:600">If you do not have a will, go to</p>
      <p class="link-lg" style="margin-top:6px">www.WillWright.example</p>
      <p style="margin-top:6px">In 20 minutes you can have a legal will – for free.</p>
      <p class="contact-h" style="margin-top:24px">CONTACT US</p>
      <p style="margin-top:8px">Have more question? Please contact us at Meadowlark and Allied Services</p>
      <p style="margin-top:16px;font-weight:600">2250 Juniper Ave. Suite 6 Riverton, ND 58000</p>
      <p class="phone" style="margin-top:14px">555-014-2200 (ext. 100)</p>
      <p style="margin-top:10px;font-weight:600">jmorrow@meadowlarkas.org | www.meadowlarkas.org</p>
    </div>
  </article>

  <!-- Front cover -->
  <article class="panel">
    <div class="panel-bg" style="background:linear-gradient(200deg,#6b4a35 0%,var(--umber) 45%,#2a2320 100%)" role="img" aria-label="Dark warm photo of an older hand held in a younger hand"></div>
    <div class="panel-bg" style="top:400px;background:linear-gradient(180deg,#f4f5f6,#e6e8ea)"></div>
    <svg style="position:absolute;left:0;top:340px" width="380" height="90" viewBox="0 0 380 90" aria-hidden="true">
      <path d="M0 38C120 58 260 40 380 8V34C260 68 120 82 0 64Z" fill="var(--green)"/>
      <path d="M0 64C120 82 260 68 380 34V90H0Z" fill="#f4f5f6"/>
    </svg>
    <div class="copy center" style="top:54px">
      <div class="brand-row"><span class="brand-dot"></span><span class="brand">MEADOWLARK</span></div>
      <p class="tag" style="margin-top:34px">Transform Your Giving</p>
      <h1 class="headline">BE STRATEGIC,<br>BE SMART</h1>
      <p class="sub">Discover the impact of Smart Giving with Meadowlark and Allied Services</p>
    </div>
    <svg style="position:absolute;left:0;top:420px" width="380" height="456" viewBox="0 0 380 456" aria-hidden="true">
      <circle cx="190" cy="230" r="165" fill="none" stroke="var(--navy)" stroke-width="2.5" stroke-dasharray="7 7"/>
      <g fill="#fff" stroke="#d9d9d9" stroke-width="1">
        <circle cx="190" cy="65" r="24"/>
        <circle cx="52" cy="140" r="24"/>
        <circle cx="328" cy="140" r="24"/>
        <circle cx="40" cy="300" r="24"/>
        <circle cx="340" cy="300" r="24"/>
        <circle cx="190" cy="395" r="26"/>
      </g>
      <g fill="none" stroke="var(--accent)" stroke-width="2" stroke-linecap="round">
        <circle cx="190" cy="65" r="11" stroke="var(--navy)"/>
        <path d="M184 65h12M190 59v12" stroke="var(--navy)"/>
        <path d="M40 134l12-8 12 8M42 136v12M48 136v12M56 136v12M62 136v12M40 150h24"/>
        <path d="M318 130h20v18h-20zM328 136c-3-4-8 0-4 4l4 4 4-4c4-4-1-8-4-4z"/>
        <path d="M30 312v-8M36 312v-12M42 312v-10M48 312v-16M28 314h24"/>
        <path d="M340 314v-16M340 302l-8-6M340 306l8-6M332 296a8 8 0 1 1 16 0" stroke="var(--green-dark)"/>
        <path d="M178 392h24v14h-24zM176 386h28v6h-28zM190 386v20M184 380c2 4 6 6 6 6s4-2 6-6"/>
      </g>
    </svg>
    <div class="photo" role="img" aria-label="Photo of a smiling young man in glasses and a red plaid shirt with arms crossed" style="left:100px;width:180px;top:500px;height:300px;border-radius:90px 90px 14px 14px;background:linear-gradient(180deg,#d8d0c6 0%,#b6564a 55%,#7c2f2c 100%)"></div>
  </article>
</section>

<!-- INSIDE SPREAD -->
<section class="spread spread--inside">

  <!-- Inside left: stocks -->
  <article class="panel">
    <div class="panel-bg" style="background:linear-gradient(180deg,#fff 40%,var(--paper-soft) 100%)"></div>
    <div class="photo" role="img" aria-label="Photo of a businessman in a suit touching a glowing stock chart" style="left:0;right:0;top:0;height:320px;background:radial-gradient(circle at 70% 55%,#6a5a3a 0%,#2a3138 40%,#11161a 100%)"></div>
    <svg style="position:absolute;left:0;top:250px" width="380" height="90" viewBox="0 0 380 90" aria-hidden="true">
      <path d="M0 30C110 70 250 70 380 20V38C250 86 110 88 0 48Z" fill="var(--green)"/>
      <path d="M0 48C110 88 250 86 380 38V90H0Z" fill="#fff"/>
    </svg>
    <div class="copy" style="top:350px">
      <p>We would like to introduce you to five Strategic and Smart ways to give that could potentially be more beneficial to you compared to traditional cash donations. We encourage you to keep this information as a guide for your future contributions.</p>
      <h3 class="sect green" style="margin-top:20px">Gifts of Stocks or Appreciated Assets Strategic &amp; Smart</h3>
      <p class="kicker navy" style="margin-top:18px">Consider your long-term publicly traded stock as a way to give to your favorite charity.</p>
      <p style="margin-top:14px">You can make a significantly bigger impact when you donate long-term appreciated securities, including stock, mutual funds, and bonds, directly to your favorite charity.</p>
      <h4 class="how navy">How Does It Work?</h4>
      <p>When you donate stock to a charity, you will generally take a tax deduction for the full market value. Because you are donating stock, your contribution and tax deduction may be significantly higher than contributing the after-tax proceeds. The same benefits apply when you donate mutual funds or bonds.</p>
    </div>
  </article>

  <!-- Inside middle: DAF and QCD -->
  <article class="panel">
    <div class="panel-bg" style="background:var(--navy)"></div>
    <div class="panel-bg" style="top:540px;background:var(--green)"></div>
    <svg style="position:absolute;left:0;top:500px" width="380" height="60" viewBox="0 0 380 60" aria-hidden="true">
      <path d="M0 38C130 6 260 0 380 14V60H0Z" fill="#fff"/>
      <path d="M0 46C130 16 260 10 380 24V60H0Z" fill="var(--green)"/>
    </svg>
    <div class="copy center white" style="top:40px">
      <h3 class="sect" style="font-size:21px">Donor-Advised Fund (DAF)<br>Strategic &amp; Smart</h3>
      <p class="kicker" style="margin-top:20px;font-size:14px">Consider a DAF – a simple, flexible, and tax-advantageous way to give to your favorite charities.</p>
      <p style="margin-top:24px">A Donor-Advised Fund (DAF), is like a charitable investment account for the sole purpose of supporting your favorite charities.</p>
      <h4 class="how" style="margin-top:24px">How Does It Work?</h4>
      <p>You establish a DAF and contribute cash, stocks, or non-publicly traded assets, cryptocurrency, and private company stock to be eligible for an immediate tax deduction. Those funds are contributed for tax-free growth. You can recommend grants be made from your DAF to any IRS qualified public charity.</p>
    </div>
    <div class="copy white qcd" style="top:566px;left:22px;right:22px">
      <h3 class="sect-sm">Qualified Charitable Distributions (QCDs)<br>Strategic &amp; Smart</h3>
      <p class="kicker-sm">Consider a QCD – when planning your IRA with drawal strategy…and donate to your favorite charity</p>
      <p class="qcd-body" style="margin-top:8px">IRA owners at age 70 ½ or over can transfer dollars from their IRA to charity tax-free each year. These transfers known as Qualified Charitable Distributions (QCDs) offer eligible older Americans a great way to easily give to charity.</p>
      <h4 class="how-sm">How Does It Work?</h4>
      <p class="qcd-body">Are you 72 and required to take a minimum distribution (RMD) from your IRA but do not need the funds? Consider a Qualified Charitable Distribution. Normally, distributions from a traditional IRA are taxable when received. With a QCD, these distributions become tax-free when paid directly from the IRA to your favorite eligible charity. An IRA owner wishing to make a QCD should contact their IRA trustee, allowing time to complete the transaction before the end of the year to receive the tax benefit.</p>
    </div>
  </article>

  <!-- Inside right: crypto and annuity -->
  <article class="panel">
    <div class="panel-bg" style="background:#fff"></div>
    <div class="copy small" style="top:24px">
      <h3 class="sect-sm green">Cryptocurrency Strategic &amp; Smart</h3>
      <p class="kicker-sm navy">Consider donating Bitcoin and other cryptocurrencies to your favorite charity.</p>
      <p style="margin-top:14px">Bitcoin and other cryptocurrencies can be donated to charity just like other appreciated assets such as stocks and other business interests. Before you sell bitcoin and donate the after-tax proceeds, consider donating your bitcoin directly to a favorite charity.</p>
      <h4 class="how-sm navy">How Does It Work?</h4>
      <p>Many donors find it useful to open a Donor-Advised Fund (DAF). This strategy includes two significant benefits, both for you and your favorite charity.</p>
      <ul class="dots">
        <li>Your tax deduction will be equal to the fair market value of the donated bitcoin (as determined by a qualified appraisal).</li>
        <li>Your cryptocurrency donation is tax-smart because it may eliminate capital gains taxes on the value / appreciation AND your favorite charity will receive 100% of the value of the contribution.</li>
      </ul>
      <p>Often charities are not able to accept direct donations of bitcoin/crypto so using a DAF is a great way to donate these assets.</p>
      <h3 class="sect-sm green" style="margin-top:26px">Charitable Gift Annuity Strategic &amp; Smart</h3>
      <p class="kicker-sm navy">Consider establishing a Charitable Gift Annuity</p>
      <p style="margin-top:14px">You make a donation to a single charity. The gift is set aside in a reserve account and invested.</p>
      <h4 class="how-sm navy">How Does It Work?</h4>
      <p>A charitable gift annuity is a contract between a donor and a charity. As a donor, you make a sizable gift to charity using cash, securities, or possibly other assets. This money is then invested.</p>
      <p style="margin-top:14px">In return, you become eligible to take a partial tax deduction for your donation, plus you receive a fixed stream of income from the charity for the rest of your life. At the end of your life (as well as your spouse's, if you're giving as a couple), the charity receives the remainder of the gift.</p>
    </div>
  </article>
</section>

</body>
</html>
```